New web design for a service provider in the medical field

We are looking for a new design for our website. We are a company that repairs and sells medical endoscopes. Our customers include doctors and hospitals. Our current website can be found at https://lumavex.de/en/lumavex-english.
We need a new web design (without programming) for the following 3 pages:
-Startpage https://lumavex.de/en/lumavex-english/
-Used endoscopes https://lumavex.de/en/used-endoscopes/
-Purchase https://lumavex.de/en/purchase/
The design should be modern and stylish.
The blue color of the logo should be reflected on the page, but not too intrusive.
I have uploaded the images from the header. If more images are needed, let me know and I will upload them.

Target Market(s)
Doctors and hospitals

```html
<!DOCTYPE html>
<html lang="en">
<head>
<meta charset="utf-8">
<title>Lumavex – Endoscope Repair &amp; Sale</title>
<link href="https://fonts.googleapis.com/css2?family=Mulish:wght@400;600;700;800&family=Montserrat:wght@600;700;800&display=swap" rel="stylesheet">
<style>
:root{
  --blue:#29a3dd;
  --blue-dark:#1d8cc4;
  --navy:#1b3447;
  --navy-deep:#203a4e;
  --ink:#2a3a48;
  --muted:#5d6b77;
  --light:#e8edf1;
  --white:#ffffff;
}
*{box-sizing:border-box;margin:0;padding:0}
html,body{width:1200px;height:4684px;overflow:hidden}
body{position:relative;font-family:"Mulish",sans-serif;color:var(--ink);background:var(--white)}
.abs{position:absolute}
h1,h2,h3,.heading{font-family:"Montserrat",sans-serif}
.btn{position:absolute;display:flex;align-items:center;justify-content:center;font-family:"Montserrat",sans-serif;font-weight:700;font-size:11px;letter-spacing:.3px;color:#fff;text-transform:uppercase;box-shadow:4px 4px 0 var(--navy)}
.btn-blue{background:var(--blue)}
.btn-navy{background:var(--navy);box-shadow:4px 4px 0 #fff}
.section-title{position:absolute;left:0;width:1200px;text-align:center;font-family:"Montserrat",sans-serif;font-weight:800;font-size:33px;color:var(--navy);text-transform:uppercase}
.section-title span{color:var(--blue)}
.title-rule{position:absolute;left:560px;width:80px;height:3px;background:var(--blue)}
.centered-text{position:absolute;left:0;width:1200px;text-align:center;font-size:18px;line-height:32px;color:var(--muted)}

/* header */
.site-header{left:0;top:0;width:1200px;height:115px;background:#fff}
.topbar{left:709px;top:0;width:491px;height:40px}
.topbar-item{position:absolute;top:12px;color:#fff;font-size:12px;font-weight:700;display:flex;align-items:center;gap:6px}
.logo-badge{left:78px;top:-40px;width:200px;height:175px;border-radius:50%;background:#fff;box-shadow:0 4px 10px rgba(0,0,0,.06)}
.logo{position:absolute;display:flex;align-items:center;gap:8px;font-family:"Mulish",sans-serif;font-weight:800;color:var(--navy)}
.logo i{display:block;border-radius:50%;background:var(--blue)}
.nav-link{position:absolute;top:70px;font-family:"Montserrat",sans-serif;font-weight:700;font-size:11.5px;color:var(--navy)}
.nav-active{position:absolute;left:305px;top:88px;width:128px;height:2px;background:var(--blue)}

/* hero */
.hero{left:0;top:115px;width:1200px;height:576px;background:linear-gradient(100deg,#c9d3da 0%,#eef1f3 40%,#dfe5e9 70%,#b9c4cc 100%)}
.hero-text{position:absolute;left:91px;width:483px;text-align:center;color:#fff}

/* intro */
.intro-heading{left:153px;top:1030px;width:480px;font-family:"Montserrat",sans-serif;font-weight:700;font-size:25px;line-height:35px;color:var(--navy)}
.intro-body{left:157px;width:460px;font-size:14px;line-height:23.5px;color:var(--ink)}

/* repair & sale */
.services{left:0;top:1455px;width:1200px;height:636px;background:var(--light)}
.card{position:absolute;top:1736px;height:287px}
.card-bordered{border:2px solid var(--blue);background:var(--light)}
.card-plain{background:#fff}
.card-icon{position:absolute;top:-40px;left:32px;width:88px;height:84px;background:var(--blue);box-shadow:6px 6px 0 var(--navy)}
.card h3{position:absolute;left:38px;top:84px;font-size:18px;font-weight:800;color:var(--navy)}
.card .sub{position:absolute;left:38px;top:106px;font-size:16px;color:var(--navy)}
.card p{position:absolute;left:38px;top:134px;width:240px;font-size:11px;line-height:15px;color:var(--ink)}
.card .btn{left:38px;top:220px;width:124px;height:32px;font-size:10px}

/* faulty */
.faulty{left:0;top:2091px;width:1200px;height:449px;background:linear-gradient(160deg,#3fb0e4 0%,#2a9ad6 45%,#1b86c9 100%)}
.faulty-text{position:absolute;left:0;width:1200px;text-align:center;color:#fff}

/* outcome grid */
.feature{position:absolute;width:320px;height:130px}
.feature-icon{position:absolute;left:14px;top:6px;width:48px;height:48px;border:2.5px solid var(--blue);border-radius:50%}
.feature-icon::after{content:"";position:absolute;left:12px;top:12px;width:19px;height:19px;border:2px solid var(--navy);border-radius:4px}
.feature h4{position:absolute;left:78px;top:4px;width:220px;font-family:"Montserrat",sans-serif;font-weight:700;font-size:18px;line-height:20px;color:var(--navy)}
.feature p{position:absolute;left:78px;width:220px;font-size:14px;line-height:19px;color:var(--ink)}
.grid-line{position:absolute;background:#d8dee3}

/* dark section */
.decision{left:0;top:3109px;width:1200px;height:658px;background:var(--navy-deep)}
.decision-title{position:absolute;left:0;top:3177px;width:1200px;text-align:center;font-family:"Montserrat",sans-serif;font-weight:800;font-size:26px;line-height:32px;color:#fff}
.point{position:absolute;width:290px;color:#fff}
.point b{display:block;font-family:"Montserrat",sans-serif;font-size:13.5px;font-weight:700;margin-bottom:4px}
.point span{display:block;font-size:9.5px;line-height:15px;color:#c7d3dc}
.point.left{text-align:right}

/* help form */
.help{left:0;top:3767px;width:1200px;height:515px;background:linear-gradient(120deg,#2c9fd9 0%,#3cb1e6 50%,#2a9bd6 100%)}
.field{position:absolute;left:220px;width:395px;height:44px;background:#fff;display:flex;align-items:center;gap:10px;padding-left:20px;font-size:13px;font-weight:700;color:var(--navy)}
.field svg{flex:none}

/* footer */
.footer-col{position:absolute;top:4390px;padding-left:18px;border-left:3px solid var(--blue)}
.footer-col h5{font-family:"Montserrat",sans-serif;font-weight:700;font-size:14px;color:var(--navy);margin-bottom:14px}
.footer-col a{display:block;font-size:13.5px;line-height:29px;color:var(--ink);text-decoration:none}
.social{display:inline-block;width:28px;height:28px;border-radius:50%;background:var(--navy);margin-right:4px}
</style>
</head>
<body>

<!-- HEADER -->
<header class="abs site-header">
  <svg class="abs topbar" viewBox="0 0 491 40" width="491" height="40"><polygon points="22,0 491,0 491,40 0,40" fill="#29a3dd"/></svg>
  <div class="topbar-item" style="left:708px">
    <svg width="18" height="18" viewBox="0 0 18 18"><circle cx="9" cy="9" r="9" fill="#fff"/><rect x="4.5" y="5.5" width="9" height="7" rx="1" fill="none" stroke="#29a3dd" stroke-width="1.4"/><path d="M4.5 6 9 9.5 13.5 6" fill="none" stroke="#29a3dd" stroke-width="1.4"/></svg>
    info@lumavex.de
  </div>
  <div class="topbar-item" style="left:880px">
    <svg width="18" height="18" viewBox="0 0 18 18"><circle cx="9" cy="9" r="9" fill="#fff"/><path d="M6 4.5c-.8.5-1.3 1.4-.9 2.6 1 2.9 3 4.9 5.8 5.9 1.2.4 2.1-.1 2.6-.9l-1.8-1.6-1.3.8c-1.2-.6-2.1-1.5-2.7-2.7l.8-1.3z" fill="#29a3dd"/></svg>
    +49 4021 555 318-0
  </div>
  <div class="topbar-item" style="left:1048px">ENG
    <svg width="10" height="8" viewBox="0 0 10 8"><path d="M1 2l4 4 4-4" fill="none" stroke="#fff" stroke-width="1.6"/></svg>
  </div>

  <div class="abs logo-badge"></div>
  <div class="logo" style="left:108px;top:44px;font-size:27px"><span>Lumavex</span><i style="width:14px;height:14px"></i></div>

  <nav>
    <a class="nav-link" style="left:305px">ENDOSCOPE REPAIR</a>
    <a class="nav-link" style="left:460px">ENDOSCOPY SYSTEMS</a>
    <a class="nav-link" style="left:627px">ENDOSCOPY ACCESSORIES
      <svg width="10" height="8" viewBox="0 0 10 8"><path d="M1 2l4 4 4-4" fill="none" stroke="#1b3447" stroke-width="1.6"/></svg></a>
    <a class="nav-link" style="left:833px">ACCESSORIES CATALOG</a>
    <a class="nav-link" style="left:1024px">PURCHASE</a>
    <div class="nav-active"></div>
  </nav>
</header>

<!-- HERO -->
<section class="abs hero" role="img" aria-label="Photo of a flexible medical endoscope handpiece with control wheels, shown in close-up on a light background"></section>
<svg class="abs" style="left:85px;top:203px" width="496" height="431" viewBox="0 0 496 431">
  <polygon points="6,215 115,6 381,6 490,215 381,425 115,425" fill="#183347" stroke="#ffffff" stroke-opacity=".25" stroke-width="2"/>
  <polygon points="16,215 121,16 375,16 480,215 375,415 121,415" fill="none" stroke="#29a3dd" stroke-width="2"/>
</svg>
<div class="hero-text" style="top:341px;font-size:19px;font-weight:400;color:var(--blue)">WELCOME TO LUMAVEX</div>
<div class="hero-text" style="top:370px;font-family:'Montserrat',sans-serif;font-weight:800;font-size:32px;line-height:41px">PUT YOUR ENDOSCOPE<br>IN RELIABLE HANDS!</div>
<a class="btn btn-blue" style="left:260px;top:469px;width:142px;height:40px;box-shadow:4px 4px 0 #fff">Learn more</a>

<!-- INTRO -->
<h2 class="section-title" style="top:768px">Your future <span>our service</span></h2>
<div class="title-rule" style="top:820px"></div>
<p class="centered-text" style="top:838px;font-size:18.5px">Lumavex GmbH is specialised in the repair and sale of Olvara, Pextona<br>and Fujara flexible medical endoscopes. As a service-oriented company, we<br>are at your side with our knowledge and skills!</p>

<h3 class="abs intro-heading">Endoscope repairs and second hand endoscopes from Lumavex cause the outcome matters!</h3>
<p class="abs intro-body" style="top:1153px">Lumavex is a privileged partner for the start-up facility or optimisation of existing healthcare facilities, doctor's offices and hospitals. The quality and reliability of our products and our offered service are our best advertisement!</p>
<p class="abs intro-body" style="top:1257px">As a result of optimised processes and highly qualified specialists in our company, we can work very quickly and with high quality for your benefit of least possible restrictions in your doctor's office or in your hospital.</p>

<div class="abs" style="left:656px;top:1225px;width:424px;height:134px;background:var(--blue)"></div>
<div class="abs" style="left:664px;top:978px;width:408px;height:372px;border:2px solid var(--blue);background:#fff"></div>
<div class="abs" role="img" aria-label="Photo of a flexible endoscope with coiled insertion tube and control body" style="left:674px;top:988px;width:388px;height:355px;background:linear-gradient(135deg,#eceef0 0%,#cfd4d8 55%,#9aa2a8 100%)"></div>

<!-- REPAIR & SALE -->
<section class="abs services"></section>
<h2 class="section-title" style="top:1518px">Repair &amp; sale endoscope</h2>
<div class="title-rule" style="top:1565px"></div>
<p class="centered-text" style="top:1578px;font-size:16px;line-height:24px;color:var(--ink)">Lorem ipsum dolor sit amet, consectetur adipiscing elit, sed do eiusmod tempor incidi-<br>dunt ut labore et dolore magna aliqua. Ut enim ad minim veniam</p>

<div class="card card-bordered" style="left:147px;width:300px">
  <div class="card-icon" role="img" aria-label="Icon of a coiled endoscope"></div>
  <h3>REPAIR</h3><div class="sub">Endoscope repair service</div>
  <p>We are very interested in buying your old endoscopes – even defective and dis-mantled! We offer fair conditions! Please contact us for a purchase offer!</p>
  <a class="btn btn-blue">Learn more</a>
</div>
<div class="card card-plain" style="left:460px;width:296px">
  <div class="card-icon" role="img" aria-label="Icon of an endoscope handpiece"></div>
  <h3>SALE</h3><div class="sub">Used endoscopes</div>
  <p>We are very interested in buying your old endoscopes – even defective and dis-mantled! We offer fair conditions! Please contact us for a purchase offer!</p>
  <a class="btn btn-blue">Learn more</a>
</div>
<div class="card card-bordered" style="left:765px;width:300px">
  <div class="card-icon" role="img" aria-label="Icon of an endoscope control body"></div>
  <h3>PURCHASE</h3><div class="sub">Used endoscopes</div>
  <p>We are very interested in buying your old endoscopes – even defective and dis-mantled! We offer fair conditions! Please contact us for a purchase offer!</p>
  <a class="btn btn-blue">Learn more</a>
</div>

<!-- FAULTY -->
<section class="abs faulty" role="img" aria-label="Blue-tinted photo of endoscopes in a repair workshop"></section>
<h2 class="faulty-text" style="top:2190px;font-family:'Montserrat',sans-serif;font-weight:800;font-size:36px">FAULTY ENDOSCOPE?</h2>
<p class="faulty-text" style="top:2253px;font-size:23px">We ensure quick and smooth repairs!</p>
<p class="faulty-text" style="top:2298px;font-size:17px;line-height:26px">Lorem ipsum dolor sit amet, consectetur adipiscing elit, sed do eius-<br>mod tempor incididunt ut labore et dolore magna aliqua.</p>
<a class="btn btn-navy" style="left:516px;top:2374px;width:152px;height:42px">Learn more</a>

<!-- OUTCOME -->
<h2 class="section-title" style="top:2612px">Cause the <span>outcome matters</span></h2>
<div class="title-rule" style="top:2658px"></div>

<div class="grid-line" style="left:104px;top:2866px;width:1000px;height:1px"></div>
<div class="grid-line" style="left:418px;top:2736px;width:1px;height:264px"></div>
<div class="grid-line" style="left:764px;top:2736px;width:1px;height:264px"></div>

<div class="feature" style="left:104px;top:2745px"><div class="feature-icon" role="img" aria-label="Icon of a team"></div>
  <h4>One company for everyone</h4><p style="top:50px">We are a service provider for doctors and hospitals!</p></div>
<div class="feature" style="left:432px;top:2745px"><div class="feature-icon" role="img" aria-label="Icon of experienced staff"></div>
  <h4>Experience characteristics us</h4><p style="top:50px">Our team has many years of ex-perience in the business field!</p></div>
<div class="feature" style="left:786px;top:2738px"><div class="feature-icon" role="img" aria-label="Icon of an endoscope"></div>
  <h4>The product is close to our hearts</h4><p style="top:50px">We repair and sell second hand, flexible endoscopes!</p></div>
<div class="feature" style="left:112px;top:2904px"><div class="feature-icon" role="img" aria-label="Icon of a shield with a tick"></div>
  <h4>Guaranteed service</h4><p style="top:36px">You receive a six-month war-ranty on all repairs!</p></div>
<div class="feature" style="left:432px;top:2904px"><div class="feature-icon" role="img" aria-label="Icon of a hand holding a star"></div>
  <h4>Quality not quantity</h4><p style="top:36px">Reliability and durability instead of inferior replacements!</p></div>
<div class="feature" style="left:786px;top:2891px"><div class="feature-icon" role="img" aria-label="Icon of a shield with a gear"></div>
  <h4>Services for everyone</h4><p style="top:28px">Our service includes the manufacturers Olvara, Pextona and Fujara!</p></div>

<!-- DECISION -->
<section class="abs decision"></section>
<h2 class="decision-title">LUMAVEX GMBH, YOUR DECISION<br>FOR YOUR FUTURE</h2>

<svg class="abs" style="left:380px;top:3250px" width="480" height="360" viewBox="0 0 480 360">
  <polygon points="20,180 120,8 360,8 460,180 360,352 120,352" fill="none" stroke="#3c5568" stroke-width="2"/>
  <polygon points="115,180 175,70 305,70 365,180 305,290 175,290" fill="#fff"/>
  <g fill="#203a4e" stroke="#fff" stroke-width="2">
    <circle cx="129" cy="73" r="29"/><circle cx="365" cy="86" r="29"/>
    <circle cx="67" cy="182" r="29"/><circle cx="413" cy="182" r="29"/>
    <circle cx="116" cy="281" r="29"/><circle cx="360" cy="277" r="29"/>
  </g>
  <g fill="none" stroke="#29a3dd" stroke-width="2">
    <path d="M117 85l24-24M117 61l24 24"/>
    <circle cx="365" cy="86" r="10"/>
    <circle cx="67" cy="182" r="10"/><circle cx="67" cy="182" r="4"/>
    <path d="M403 190h20v-12l-10-7-10 7z"/>
    <rect x="104" y="270" width="24" height="18" rx="2"/><path d="M108 277h16M108 282h10"/>
    <path d="M348 283l6-10 6 10 6-10 6 10"/>
  </g>
</svg>
<div class="logo" style="left:548px;top:3412px;font-size:24px"><span>Lumavex</span><i style="width:11px;height:11px"></i></div>

<div class="point left" style="left:167px;top:3300px"><b>Fast Repairs</b><span>Keep potential disruptions in your doctor's<br>office or in your hospital at minimum</span></div>
<div class="point" style="left:796px;top:3306px"><b>Highly cost efficient</b><span>Benefit from our first class recommendations<br>and implementation by our experienced staff.</span></div>
<div class="point left" style="left:106px;top:3406px"><b>On-site service</b><span>We will gladly pay you a visit to to carry<br>out analysis and repairs on site. Due to our<br>many years of experience</span></div>
<div class="point" style="left:838px;top:3406px"><b>Loan equipment service</b><span>We will gladly pay you a visit to to carry<br>out analysis and repairs on site. Due to our<br>many years of experience</span></div>
<div class="point left" style="left:154px;top:3520px"><b>Without a maintenance contract</b><span>No subscription or other maintenance contract,<br>but one-time and sustainable repair work</span></div>
<div class="point" style="left:784px;top:3530px"><b>First class service</b><span>Our clients always come first!</span></div>

<a class="btn btn-blue" style="left:458px;top:3651px;width:330px;height:44px;font-size:12.5px;box-shadow:4px 4px 0 #fff">Learn more about Lumavex</a>

<!-- HELP -->
<section class="abs help" role="img" aria-label="Soft blue background with a faint DNA helix illustration"></section>
<h2 class="abs" style="left:0;top:3835px;width:1200px;text-align:center;font-weight:800;font-size:31px;color:#fff">HOW CAN WE HELP YOU?</h2>
<p class="abs" style="left:0;top:3890px;width:1200px;text-align:center;font-size:15px;line-height:21px;color:#eaf6fd">Lorem ipsum dolor sit amet, consectetur adipiscing elit, sed do eiusmod tempor incididunt<br>ut labore et dolore magna aliqua. Ut enim ad minim veniam, quis nostrud</p>

<div class="field" style="top:3978px">
  <svg width="14" height="14" viewBox="0 0 14 14"><circle cx="7" cy="4" r="3" fill="#9aa6b0"/><path d="M1 14c0-4 3-6 6-6s6 2 6 6z" fill="#9aa6b0"/></svg>First name</div>
<div class="field" style="top:4032px">
  <svg width="14" height="14" viewBox="0 0 14 14"><path d="M3 1c-1 .6-1.7 1.8-1.2 3.4 1.3 3.8 3.9 6.4 7.6 7.7 1.6.5 2.7-.1 3.4-1.2l-2.3-2.1-1.7 1c-1.6-.8-2.7-2-3.5-3.5l1-1.7z" fill="#9aa6b0"/></svg>Phone number</div>
<div class="field" style="top:4087px">
  <svg width="14" height="12" viewBox="0 0 14 12"><rect x="1" y="1" width="12" height="10" rx="1" fill="none" stroke="#9aa6b0" stroke-width="1.5"/><path d="M1 2l6 5 6-5" fill="none" stroke="#9aa6b0" stroke-width="1.5"/></svg>Email address</div>
<div class="abs" style="left:625px;top:3978px;width:397px;height:158px;background:#fff;padding:14px 22px;font-size:13px;font-weight:700;color:var(--navy)">Comments</div>
<a class="btn btn-navy" style="left:533px;top:4169px;width:162px;height:44px;font-size:12px">Submit now</a>

<!-- FOOTER -->
<footer>
  <div class="logo" style="left:127px;top:4412px;font-size:26px"><span>Lumavex</span><i style="width:13px;height:13px"></i></div>
  <p class="abs" style="left:121px;top:4505px;width:270px;font-size:12px;line-height:15px;color:var(--muted)">Lorem ipsum dolor sit amet, consectetur adipiscing elit, sed do eiusmod tempor incididunt ut labore et dolore</p>

  <div class="footer-col" style="left:464px;height:150px"><h5>NAVIGATION</h5>
    <a>Home</a><a>Endoscope Repair</a><a>Used Endoscope</a><a>Endoscopy Systems</a></div>
  <div class="footer-col" style="left:704px;height:110px"><h5>RESOURCES</h5>
    <a>Endoscopy Accesories</a><a>Purchase</a><a>Contact Us</a></div>
  <div class="footer-col" style="left:909px;height:28px"><h5>FOLLOW US</h5>
    <span class="social"></span><span class="social"></span><span class="social"></span><span class="social"></span></div>

  <div class="abs" style="left:0;top:4620px;width:1200px;height:1px;background:#dfe4e8"></div>
  <p class="abs" style="left:0;top:4641px;width:1200px;text-align:center;font-size:12px;color:var(--muted)">© 2022 Lumavex GmbH</p>
</footer>

</body>
</html>
```